Local water manufacturing needs a re-design to an existing label design.

We need to change an existing label design for an established water manufacturing company located in the Bahamas. We are expanding into a new 1.5L size product and would like to do so with an updated label design that incorporates an animated pink conch shell (sample included) with at least one other bright color to match the existing blue background and the pink conch shell. The final design should convey an island feel and vibe. The existing label is only a suggestion. The entire label can be completely changed.

Target Market(s)

Hotels, tourist

Industry/Entity Type

Water Manufacturing

Requirements
Must have
• Bright color that matches blue cap and pink conch shell
Nice to have
• Simple design with sleek modern look.

```html
<!DOCTYPE html>
<html lang="en">
<head>
<meta charset="UTF-8">
<title>Coralis Purified Water Label</title>
<link rel="stylesheet" href="https://fonts.googleapis.com/css2?family=Poppins:wght@400;500;600;700;800&family=Roboto+Condensed:wght@400&display=swap">
<style>
  :root {
    --sky-top: #8fe3f8;
    --sky-mid: #e6f8fd;
    --sky-low: #ffffff;
    --sea-deep: #06b3cf;
    --sea-light: #5fd9ea;
    --sand: #f7dcaa;
    --sand-light: #fbe9c6;
    --magenta: #cc1190;
    --cream: #fbeee2;
    --navy: #0f2e52;
    --card: #ffffff;
  }
  * { margin: 0; padding: 0; box-sizing: border-box; }
  html, body { width: 960px; height: 1200px; overflow: hidden; }
  body { font-family: "Poppins", sans-serif; color: var(--navy); }

  .label {
    position: relative; width: 960px; height: 1200px; overflow: hidden;
    background: linear-gradient(180deg, var(--sky-top) 0%, var(--sky-mid) 18%, var(--sky-low) 40%, var(--sky-low) 51%, #f2fbfe 51.6%);
  }
  .beach-scene {
    position: absolute; left: 0; top: 618px; width: 960px; height: 582px;
    background: linear-gradient(180deg, #0aa9c6 0%, var(--sea-deep) 4%, #25c8e0 14%, var(--sea-light) 22%, #bfeef3 26%, var(--sand-light) 29%, var(--sand) 45%, var(--sand-light) 100%);
  }

  .brand-band {
    position: absolute; left: 272px; top: 182px; width: 580px; height: 202px;
    background: var(--magenta); border-radius: 0 40px 40px 0;
  }
  .brand-name {
    position: absolute; left: 342px; top: 196px; width: 500px; height: 176px;
    font-weight: 600; font-size: 124px; line-height: 176px; color: var(--cream);
    letter-spacing: -2px;
  }
  .conch {
    position: absolute; left: 96px; top: 148px; width: 240px; height: 288px;
    border-radius: 46% 54% 40% 60% / 50% 38% 62% 50%;
    background: radial-gradient(ellipse at 55% 60%, #f48cc6 0%, #f9c6dc 40%, #fbe7e4 75%);
    border: 3px solid var(--magenta);
  }
  .product-type {
    position: absolute; left: 360px; top: 410px; width: 390px; text-align: center;
    font-weight: 600; font-size: 47px; line-height: 56px; color: var(--navy);
  }
  .product-note {
    position: absolute; left: 360px; top: 470px; width: 390px; text-align: center;
    font-weight: 400; font-size: 28px; line-height: 36px; letter-spacing: 2px; color: var(--navy);
  }

  .info-card {
    position: absolute; left: 110px; top: 666px; width: 742px; height: 560px;
    border-radius: 40px 40px 0 0;
    background: linear-gradient(180deg, var(--card) 0%, var(--card) 40%, rgba(255,255,255,0.5) 70%, rgba(255,255,255,0) 92%);
  }

  .nutrition {
    position: absolute; left: 176px; top: 712px; width: 264px;
    font-family: "Roboto Condensed", sans-serif; font-size: 12.5px; color: var(--navy);
  }
  .nutrition-title {
    font-family: "Poppins", sans-serif; font-weight: 800; font-size: 31px;
    line-height: 36px; letter-spacing: 0.5px; margin-left: -2px; margin-bottom: 2px;
  }
  .nutrition .row { height: 18px; line-height: 18px; display: flex; }
  .nutrition .row .leader { flex: 1; overflow: hidden; white-space: nowrap; letter-spacing: 2px; padding-left: 2px; }
  .nutrition .row .pct { width: 14px; text-align: right; }
  .nutrition .row.right { justify-content: flex-end; }
  .rule-thick { height: 4px; background: var(--navy); margin: 6px 0 4px; }
  .rule { height: 2px; background: var(--navy); margin: 4px 0; }
  .nutrition .foot { font-size: 12px; line-height: 18px; margin-top: 2px; white-space: nowrap; }

  .company {
    position: absolute; left: 504px; top: 712px; width: 300px; color: var(--navy);
  }
  .company h2 { font-weight: 700; font-size: 23px; line-height: 34px; }
  .company p { font-weight: 400; font-size: 20px; line-height: 28.5px; }
  .company .contact-heading { margin-top: 16px; }
</style>
</head>
<body>
<main class="label">
  <div class="beach-scene" role="img" aria-label="Illustrated beach with turquoise sea, sand, starfish and seashells"></div>

  <div class="brand-band"></div>
  <div class="brand-name">Coralis</div>
  <div class="conch" role="img" aria-label="Illustrated pink conch shell"></div>

  <div class="product-type">PURIFIED WATER</div>
  <div class="product-note">MINERALS ADDED</div>

  <section class="info-card"></section>

  <section class="nutrition">
    <h2 class="nutrition-title">Nutrition Facts</h2>
    <div class="row">Serving Size&nbsp;&nbsp;&nbsp;&nbsp;ml</div>
    <div class="row">Serving Per Container</div>
    <div class="rule-thick"></div>
    <div class="row">Amount Per Serving</div>
    <div class="row">Calories&nbsp;&nbsp;&nbsp;&nbsp;Cal</div>
    <div class="rule-thick"></div>
    <div class="row right">% Daily Value*</div>
    <div class="rule"></div>
    <div class="row">Total Fat&nbsp;&nbsp;&nbsp;&nbsp;g<span class="leader">..............................</span><span class="pct">%*</span></div>
    <div class="row">Satured Fat&nbsp;&nbsp;&nbsp;&nbsp;g<span class="leader">..............................</span><span class="pct">%*</span></div>
    <div class="rule"></div>
    <div class="row">Sodium&nbsp;&nbsp;&nbsp;&nbsp;mg<span class="leader">..............................</span><span class="pct">%*</span></div>
    <div class="rule"></div>
    <div class="row">Total Carb&nbsp;&nbsp;&nbsp;&nbsp;g<span class="leader">..............................</span><span class="pct">%*</span></div>
    <div class="row">Dietary Fiber&nbsp;&nbsp;&nbsp;&nbsp;g<span class="leader">..............................</span><span class="pct">%*</span></div>
    <div class="row">Sugars&nbsp;&nbsp;&nbsp;&nbsp;g</div>
    <div class="rule"></div>
    <div class="row">Protein&nbsp;&nbsp;&nbsp;&nbsp;g</div>
    <div class="rule"></div>
    <div class="foot">*Percent Daily Values are based on a (&nbsp;&nbsp;&nbsp;&nbsp;&nbsp;) calorie diet.</div>
  </section>

  <section class="company">
    <h2>Bottled by:</h2>
    <p>CB Ltd, t/a Coralis Water<br>&amp; Lumen Water .<br>PO BOX CR-10482</p>
    <h2 class="contact-heading">Call For More Info:</h2>
    <p>sales:555-0142<br>office:55-0190</p>
  </section>
</main>
</body>
</html>
```